Business cards in digital learning for freelancer

Hello, I need a business cards in french. I work in the Digital learning industries as freeelancer; I'm an expert in digital learning. I work in France. My customer are in the health industry, pharmaceutical industry, and training organization. I've got a logo. I offer three services: consulting, Design, and Training. In the consulting, I offers coaching to choose your digital learning tools and the digital learning strategy. For the Design, I product differents level of elearning like rapid-learning, elearning, micro-learning, video-learning. And for the training service, I've create training about pedagogy, digital learning management project, Digital learning design.
I join my Logo create in this platform. My universe is gamified. I like the life, and I'm very social. I want a card like I'm I. I love Art (painting), Europeen comics. I use in my visual support "permanent maker" font and caracters. I would like cards: elegant, modern, Top class. If you need any information, you can ask me.
thanks for ideas

Target Market(s)

in health industries and training organization for Training manager, instructor, human resources director

Contact Information for Business Card

Phone number : 06 71 38 95 14 , mail: bastiengolmier@quelmoto.fr, web: bastiengolmier.fr , Carrivo

Font styles to use
Sans Serif

Requirements
Must have
• Use my logo and write my 3 services (consulting, training, design)

```html
<!DOCTYPE html>
<html lang="fr">
<head>
<meta charset="utf-8">
<title>Golmier Digital Learning – Cartes de visite</title>
<link rel="stylesheet" href="https://fonts.googleapis.com/css2?family=Montserrat:wght@600;800&family=Arimo:wght@400;700&display=swap">
<style>
  :root {
    --orange: #f07426;
    --white: #ffffff;
    --ink: #3c3c3c;
    --grey: #6b6b6b;
    --backdrop: #d9d9d9;
  }
  * { box-sizing: border-box; margin: 0; padding: 0; }
  html, body { width: 1200px; height: 900px; overflow: hidden; }
  body {
    background: var(--backdrop);
    font-family: "Arimo", Arial, sans-serif;
    display: flex;
    flex-direction: column;
    align-items: center;
    justify-content: center;
    gap: 60px;
  }
  .card {
    width: 580px;
    height: 330px;
    position: relative;
    box-shadow: 0 6px 18px rgba(0,0,0,.18);
    overflow: hidden;
  }

  /* Front */
  .card--front {
    background: var(--orange);
    color: var(--white);
    display: flex;
    flex-direction: column;
    align-items: center;
    justify-content: center;
  }
  .brand-name {
    font-family: "Montserrat", Arial, sans-serif;
    font-weight: 800;
    font-size: 52px;
    letter-spacing: 3px;
    line-height: 1;
    display: flex;
    align-items: center;
    gap: 14px;
    white-space: nowrap;
  }
  .brand-name .brand-dot {
    width: 22px; height: 22px; border-radius: 50%;
    background: currentColor;
    flex: none;
  }
  .brand-sub {
    font-family: "Montserrat", Arial, sans-serif;
    font-weight: 800;
    font-size: 15px;
    letter-spacing: 4px;
    margin-top: 10px;
    text-transform: uppercase;
  }
  .services {
    list-style: none;
    display: flex;
    gap: 34px;
    margin-top: 46px;
    font-size: 20px;
    letter-spacing: 2.5px;
  }
  .services li::before {
    content: "";
    display: inline-block;
    width: 7px; height: 7px; border-radius: 50%;
    background: var(--white);
    margin-right: 8px;
    vertical-align: middle;
  }

  /* Back */
  .card--back { background: var(--white); }
  .identity {
    position: absolute;
    left: 0; top: 150px;
    display: flex;
    align-items: stretch;
    gap: 20px;
  }
  .identity__bar { width: 18px; background: var(--orange); }
  .identity__name {
    font-family: "Montserrat", Arial, sans-serif;
    font-weight: 800;
    font-size: 24px;
    color: var(--orange);
    letter-spacing: .5px;
    line-height: 1.05;
    white-space: nowrap;
  }
  .identity__role { font-size: 16px; color: var(--ink); margin-top: 3px; }

  .brand--back {
    position: absolute;
    right: 34px; top: 56px;
    width: 220px;
    color: var(--orange);
    text-align: right;
  }
  .brand--back .brand-name { font-size: 34px; gap: 9px; justify-content: flex-end; letter-spacing: 2px; }
  .brand--back .brand-name .brand-dot { width: 14px; height: 14px; }
  .brand--back .brand-sub { font-size: 10px; letter-spacing: 3px; margin-top: 8px; }

  .contacts {
    position: absolute;
    left: 120px; bottom: 34px;
    list-style: none;
    font-size: 15px;
    color: var(--ink);
    line-height: 1.5;
  }
  .contacts li { display: flex; align-items: center; gap: 8px; }
  .contacts svg { width: 13px; height: 13px; fill: var(--orange); flex: none; }
  .contact-circle { width: 13px; height: 13px; border-radius: 50%; background: var(--orange); flex: none; }
</style>
</head>
<body>

  <section class="card card--front" aria-label="Recto">
    <div class="brand-name"><span class="brand-dot"></span>GOLMIER</div>
    <div class="brand-sub">Digital Learning</div>
    <ul class="services">
      <li>Consulting</li>
      <li>Training</li>
      <li>Design</li>
    </ul>
  </section>

  <section class="card card--back" aria-label="Verso">
    <div class="identity">
      <span class="identity__bar"></span>
      <div>
        <p class="identity__name">BASTIEN GOLMIER</p>
        <p class="identity__role">Creative Director</p>
      </div>
    </div>

    <div class="brand--back">
      <div class="brand-name"><span class="brand-dot"></span>GOLMIER</div>
      <div class="brand-sub">Digital Learning</div>
    </div>

    <ul class="contacts">
      <li>
        <svg viewBox="0 0 24 24" aria-hidden="true"><path d="M6.6 10.8a15.5 15.5 0 0 0 6.6 6.6l2.2-2.2a1 1 0 0 1 1-.25 11.4 11.4 0 0 0 3.6.57 1 1 0 0 1 1 1V20a1 1 0 0 1-1 1A17 17 0 0 1 3 4a1 1 0 0 1 1-1h3.5a1 1 0 0 1 1 1c0 1.250.2 2.450.57 3.57a1 1 0 0 1-.25 1z"/></svg>
        06 71 38 95 14
      </li>
      <li>
        <svg viewBox="0 0 24 24" aria-hidden="true"><path d="M2 5h20v14H2z M2 5l10 8 10-8" stroke="#fff" stroke-width="1.5"/></svg>
        bastiengolmier@quelmoto.fr
      </li>
      <li>
        <svg viewBox="0 0 24 24" aria-hidden="true"><circle cx="12" cy="12" r="10"/><path d="M2 12h20M12 2c3 3 3 17 0 20M12 2c-3 3-3 17 0 20" stroke="#fff" stroke-width="1.3" fill="none"/></svg>
        www.bastiengolmier.fr
      </li>
      <li>
        <span class="contact-circle" aria-hidden="true"></span>
        @bastiengolmier
      </li>
    </ul>
  </section>

</body>
</html>
```